Healthy lifestyle Influencer business card

I need your creativity to have a business card that I can leave in all the restaurants, hotels and spas I visit to inform them that I am an influencer specializing in the wellness sector and that I will write a review about them. You can use my instagram photos Lunavita27 or on my website www.piattileggeriorto.it. I would like my business card to impress with its creativity! thank you very much!

Contact Information for Business Card

siteweb, instagram, phone number

Font styles to use
Decorative
Script

Colors
0094D4
00A9DD
6FCCEA
C7EBF8
E9F6FB
59FF00
82FF00
B8FF75
E3FFCB
F4FFEA
FFC000
F8CF3A
FAE287
FDF2CF
FEFAEE
F0912C
F2A743
F7CA91
FBE8D2
FDF5EE
EE7325
F08F49
F5BC92
FAE3D3
FDF4ED
EB3D1F
EC4F4E
F09395
F8D3D4
FCEDEE
E54698
E96AAD
F1A4CE
F9D9EA
FCEFF6

Requirements
Nice to have
• creativity

```html
<!DOCTYPE html>
<html lang="it">
<head>
<meta charset="utf-8">
<title>Luna Vita Cucina – Biglietto da visita</title>
<link href="https://fonts.googleapis.com/css2?family=Quicksand:wght@500;600&family=Roboto:wght@300;400&family=Saira+Condensed:wght@500&display=swap" rel="stylesheet">
<style>
  :root{
    --backdrop:#2b2b2b;
    --sage:#8fb5a9;
    --sage-light:#a6c6bb;
    --sage-deep:#7fa598;
    --ink:#3d3d3d;
    --ink-soft:#4a4a4a;
    --paper-top:#f4f4f4;
    --paper-bottom:#dcdcdc;
    --swoosh:#444444;
  }
  *{box-sizing:border-box;margin:0;padding:0}
  html,body{width:1200px;height:1138px;overflow:hidden;background:var(--backdrop)}
  .card{position:absolute;width:620px;height:376px;border-radius:16px;overflow:hidden;box-shadow:0 6px 14px rgba(0,0,0,.45)}
  .card--front{left:272px;top:184px}
  .card--back{left:274px;top:606px;background:linear-gradient(180deg,var(--paper-top),var(--paper-bottom))}
  .photo-grid{position:absolute;inset:0;background:linear-gradient(135deg,var(--sage-light),var(--sage) 55%,var(--sage-deep))}
  .brand{position:absolute;font-family:"Quicksand",sans-serif;font-weight:600;color:var(--ink);white-space:nowrap;display:flex;align-items:center;gap:12px}
  .tagline{position:absolute;font-family:"Quicksand",sans-serif;font-weight:500;color:var(--ink);white-space:nowrap}
  .handle{position:absolute;font-family:"Roboto",sans-serif;font-weight:400;color:var(--ink-soft);font-size:17px;display:flex;align-items:center;gap:12px}
  .handle__dot{width:15px;height:15px;border-radius:50%;background:var(--ink-soft)}
  .card--front .brand{left:0;right:0;top:150px;justify-content:center;font-size:44px}
  .card--front .tagline{left:0;right:0;top:208px;text-align:center;font-size:19px}
  .card--front .handle{left:228px;top:328px}
  .wave{position:absolute;inset:0}
  .owner{position:absolute;right:16px;top:34px;font-family:"Saira Condensed",sans-serif;font-weight:500;font-size:30px;color:var(--ink)}
  .card--back .brand{left:18px;top:158px;font-size:44px}
  .card--back .tagline{left:66px;top:222px;font-size:19px}
  .card--back .handle{left:37px;top:320px}
  .contacts{position:absolute;right:36px;top:272px;list-style:none;font-family:"Roboto",sans-serif;font-weight:300;font-size:16px;color:var(--ink)}
  .contacts li{display:flex;justify-content:flex-end;align-items:center;gap:22px;height:24px}
  .contacts svg{width:16px;height:16px;fill:var(--sage)}
</style>
</head>
<body>
  <section class="card card--front">
    <div class="photo-grid" role="img" aria-label="Griglia di foto di piatti sani, velata in verde salvia"></div>
    <div class="brand">Luna Vita Cucina</div>
    <p class="tagline">Sana e felice a ogni pasto</p>
    <p class="handle"><span class="handle__dot"></span>@Lunavita27</p>
  </section>

  <section class="card card--back">
    <svg class="wave" viewBox="0 0 620 376" preserveAspectRatio="none">
      <path fill="var(--sage)" d="M0,0 H620 V118 C540,128 480,112 390,70 C310,32 230,12 140,20 C80,26 35,40 0,55 Z"/>
      <path fill="#f6f6f6" d="M0,55 C35,40 80,26 140,20 C230,12 310,32 390,70 C480,112 540,128 620,118 V128 C540,138 470,122 385,80 C300,40 230,22 140,30 C80,36 35,50 0,64 Z"/>
      <path fill="var(--swoosh)" d="M0,64 C50,40 150,12 260,26 C330,35 370,60 420,88 C480,120 545,133 620,124 V140 C540,154 470,140 400,108 C330,74 250,46 150,54 C90,60 40,76 0,100 Z"/>
    </svg>
    <h1 class="owner">Luna Ferraro</h1>
    <div class="brand">Luna Vita Cucina</div>
    <p class="tagline">Sana e felice a ogni pasto</p>
    <p class="handle"><span class="handle__dot"></span>@Lunavita27</p>
    <ul class="contacts">
      <li>000-0000-0000
        <svg viewBox="0 0 16 16"><path d="M2 6c0-2 3-3 6-3s6 1 6 3v1h-3V6H5v1H2z M4 8h8l1 5H3z"/></svg></li>
      <li>info@piattileggeriorto.it
        <svg viewBox="0 0 16 16"><path d="M1 3h14v10H1z M2 4l6 5 6-5" stroke="#fff" stroke-width="1"/></svg></li>
      <li>www.piattileggeriorto.it
        <svg viewBox="0 0 16 16"><circle cx="8" cy="8" r="7"/><path d="M1 8h14M8 1v14M3 4h10M3 12h10" stroke="#fff" stroke-width=".8" fill="none"/></svg></li>
    </ul>
  </section>
</body>
</html>
```